Brightmill Data Works

Our company is about IT hardwares and IT solutions. IT hardware such as PC, RAMS, storage and servers. IT solutions such as project management, BA. We are also selling new technology too.

Target Market(s)

Consumer, Small to Medium Business, Corporate

Requirements
Must have
• The business card must have the following:
• Name:
• Title:
• Contact Number:
• Email address:
• Website:
• Color: Must match the logo color upgrade

```html
<!DOCTYPE html>
<html lang="en">
<head>
<meta charset="UTF-8">
<title>Brightmill Data Works – Business Card</title>
<link rel="stylesheet" href="https://fonts.googleapis.com/css2?family=Montserrat:wght@400;500;700;800&display=swap">
<style>
  :root {
    --stage: #161616;
    --card: #232323;
    --card-edge: #2d2d2d;
    --ink: #ffffff;
    --ink-soft: #e6e6e6;
    --accent: #e3912f;
  }
  * { box-sizing: border-box; margin: 0; padding: 0; }
  html, body {
    width: 1200px; height: 900px; overflow: hidden;
    background: var(--stage);
    font-family: "Montserrat", sans-serif;
  }
  .stage {
    width: 1200px; height: 900px;
    display: flex; flex-direction: column; align-items: center; justify-content: center;
    gap: 36px;
  }
  .card {
    width: 700px; height: 400px;
    background: linear-gradient(135deg, var(--card) 0%, var(--card-edge) 60%, var(--card) 100%);
    position: relative;
    box-shadow: 0 10px 30px rgba(0,0,0,.6);
  }
  /* Front */
  .card-front {
    display: flex; align-items: center; justify-content: center;
  }
  .wordmark {
    display: flex; align-items: center; gap: 16px;
  }
  .wordmark-dot {
    width: 22px; height: 22px; background: var(--accent);
  }
  .wordmark-name {
    font-weight: 800; font-size: 40px; letter-spacing: 1px;
    text-transform: uppercase; color: var(--ink); line-height: 1.05;
  }
  .card-front .wordmark-name { text-align: left; }
  /* Back */
  .card-back {
    display: grid; grid-template-columns: 360px 1px 1fr; align-items: center;
    padding: 0 40px 0 30px;
  }
  .card-back .wordmark { justify-content: center; gap: 12px; }
  .card-back .wordmark-dot { width: 16px; height: 16px; }
  .card-back .wordmark-name { font-size: 30px; }
  .divider { width: 2px; height: 210px; background: var(--ink-soft); }
  .details { padding-left: 34px; color: var(--ink-soft); }
  .person-name {
    font-weight: 500; font-size: 27px; color: var(--accent);
    text-transform: uppercase; line-height: 1;
  }
  .person-title { font-size: 17px; margin-top: 4px; }
  .address { font-size: 16px; line-height: 1.35; margin-top: 22px; }
  .contacts { list-style: none; margin-top: 16px; font-size: 17px; }
  .contacts li { display: flex; align-items: center; gap: 10px; line-height: 1.5; }
  .contacts svg { width: 14px; height: 14px; flex: none; }
  .accent { color: var(--accent); }
</style>
</head>
<body>
<main class="stage">
  <section class="card card-front">
    <div class="wordmark">
      <span class="wordmark-dot"></span>
      <span class="wordmark-name">Brightmill<br>Data Works</span>
    </div>
  </section>

  <section class="card card-back">
    <div class="wordmark">
      <span class="wordmark-dot"></span>
      <span class="wordmark-name">Brightmill<br>Data Works</span>
    </div>
    <div class="divider"></div>
    <div class="details">
      <p class="person-name">Daniel Hartley</p>
      <p class="person-title">Director</p>
      <p class="address">2750 Orchard Vale Rd<br>Linden, CA 95236-0418</p>
      <ul class="contacts">
        <li>
          <svg viewBox="0 0 16 16" aria-hidden="true"><path d="M4 1.5l2.2 3-1.4 1.6c.9 2 2.4 3.5 4.3 4.4l1.6-1.4 3 2.2-1.2 2.4C7.5 13.3 2.7 8.5 1.6 3z" fill="var(--accent)"/></svg>
          555-204-7713
        </li>
        <li>
          <svg viewBox="0 0 16 16" aria-hidden="true"><rect x="1.5" y="3.5" width="13" height="9" fill="none" stroke="var(--accent)" stroke-width="1.4"/><path d="M1.5 3.5L8 9l6.5-5.5" fill="none" stroke="var(--accent)" stroke-width="1.4"/></svg>
          info@brightmilldata.com
        </li>
        <li>
          <svg viewBox="0 0 16 16" aria-hidden="true"><circle cx="8" cy="8" r="6.5" fill="none" stroke="var(--accent)" stroke-width="1.3"/><ellipse cx="8" cy="8" rx="2.8" ry="6.5" fill="none" stroke="var(--accent)" stroke-width="1.1"/><path d="M1.5 8h13M2.5 4.8h11M2.5 11.2h11" stroke="var(--accent)" stroke-width="1"/></svg>
          <span>www.<span class="accent">brightmilldata</span>.com</span>
        </li>
      </ul>
    </div>
  </section>
</main>
</body>
</html>
```